Moon Tot needs ecommerce website design help

We need someone to set up a fully functional website for us. We sell baby bibs, I attached them along with our company logo (MTG: moon tot goods). The bibs are made of 100% silicon, they are safe, light weight, soft, smooth, flexible, dishwasher safe and has funny faces.

Business name: Moon Tot Goods
Elm Hollow, NY 00000
email: MoonTotGoods@mailbox-example.com
tel.: (555) 014-TOTS
website: MoonTotGoods-example.com

Target Market(s)

18-40

Industry/Entity Type

Baby

Coding

Coded - Design and coding required

Number of Pages Required

5+ page

Requirements
Must have
• 1. Pages: Why buy from us, Contact Us, Home page, Products Page, Blog
• 2. Use the colors from our logo for the web design.
• 3. Need a link that will connect visitors to our facebook, instagram, Pinterest and Tumblr account. Would like links on,the top left side of the page
Nice to have
• My Cart page
• 1. On contact us page, we want to include some type of template for the customer to complete. (Ex: name, email address, contact number, optional home address, comments)
• 2. When clients visit our website, we want a capture/pop up for the customer to subscribe to our email list to receive discounts. (Ex. Want 10% off your next order ? Suscribe to our mailing list below and get a 10% off code to use at check out. If they don't want to subscribe, they have the option to select "No Thank You, I want to pay full price).
• 3. On home page have subscribe to our email list.

```html
<!DOCTYPE html>
<html lang="en">
<head>
<meta charset="utf-8">
<title>Moon Tot Goods – Silicone Baby Bibs</title>
<link rel="stylesheet" href="https://fonts.googleapis.com/css2?family=Didact+Gothic&family=Open+Sans:wght@400;600;700&display=swap">
<style>
:root{
  --berry:#a3233b;
  --berry-deep:#6e1a2a;
  --berry-dim:#7d1d30;
  --footer:#561a25;
  --leaf:#6f8a14;
  --leaf-dim:#4f6410;
  --coral:#f24d63;
  --charcoal:#3a3a3c;
  --header:#e9e9ea;
  --page:#dedfe1;
  --ink:#2b2b2b;
  --muted:#5a5a5a;
  --mustard:#b78d2c;
  --white:#ffffff;
}
*{box-sizing:border-box;margin:0;padding:0}
html,body{width:1200px;height:2230px;overflow:hidden}
body{position:relative;background:var(--page);font-family:"Open Sans",Arial,sans-serif;color:var(--ink)}
.abs{position:absolute}
a{color:inherit;text-decoration:none}

/* top bar */
.topbar{left:0;top:0;width:1200px;height:49px;background:var(--berry-dim);color:#c79aa3;font-size:11px}
.topbar .item{position:absolute;top:17px;display:flex;align-items:center;gap:8px}
.topbar svg{fill:#c79aa3}

/* header */
.site-header{left:0;top:49px;width:1200px;height:132px;background:var(--header)}
.brand{left:131px;top:70px;display:flex;align-items:center;gap:12px}
.brand-dot{width:40px;height:40px;border-radius:50%;background:var(--leaf-dim)}
.brand-name{font-family:"Didact Gothic",sans-serif;font-size:24px;color:#1f1f1f;letter-spacing:1px}
.account{right:132px;top:79px;font-size:13px;color:var(--berry);display:flex;align-items:center;gap:10px;letter-spacing:.3px}
.cart-badge{width:30px;height:30px;border-radius:50%;background:var(--leaf-dim);display:flex;align-items:center;justify-content:center}
.main-nav{right:132px;top:131px;display:flex;gap:36px;font-size:12px;font-weight:700;color:#1e1e1e;letter-spacing:.2px}
.main-nav .current{color:var(--berry)}

/* hero */
.hero{left:0;top:181px;width:1200px;height:439px;background:linear-gradient(90deg,#c9ccd3 0%,#c5c8d0 45%,#a9acb5 62%,#c3c6cd 80%,#bfc2c9 100%)}
.hero-copy{left:132px;top:251px}
.hero-kicker{font-family:"Didact Gothic",sans-serif;font-weight:700;font-size:28px;color:var(--leaf-dim);letter-spacing:1px}
.hero-title{font-family:"Didact Gothic",sans-serif;font-size:56px;color:var(--berry-deep);font-weight:700;line-height:64px;letter-spacing:2px}
.hero-text{font-size:19px;line-height:34px;color:#2a2a2a;margin-top:2px;letter-spacing:.5px}
.btn-read{left:132px;top:468px;width:121px;height:42px;background:var(--berry-deep);color:#d7b0b8;font-size:12px;font-weight:700;display:flex;align-items:center;justify-content:center;letter-spacing:.5px}
.slider-dots{left:134px;top:543px;display:flex;gap:10px}
.slider-dots span{width:8px;height:8px;border-radius:50%;background:#9a9aa2}
.slider-dots span:first-child{background:var(--berry)}

/* why section */
.section-title{font-family:"Didact Gothic",sans-serif;font-size:30px;letter-spacing:.5px}
.section-title .lead{color:var(--leaf-dim)}
.section-title .tail{color:var(--berry-deep)}
.why-title{left:132px;top:660px}
.why-col{position:absolute;top:710px;width:299px}
.why-col p{font-size:11px;line-height:18px;color:#4b4b4b}
.why-col .more{display:block;font-size:11px;color:var(--berry);margin-top:12px}
.why-photo{position:absolute;top:795px;width:299px;height:298px;background:radial-gradient(circle at 50% 55%,#b9b4ab 0%,#c8c9cb 45%,#d2d3d5 100%)}

/* products */
.products-title{left:132px;top:1157px}
.carousel-arrows{left:1040px;top:1166px;display:flex;gap:6px}
.product{position:absolute;top:1219px;width:224px;height:330px}
.product-photo{width:100%;height:268px;background:radial-gradient(circle at 50% 48%,#c4c4c6 0%,#d4d5d7 70%)}
.product.featured .product-photo{background:#5b5b5e;position:relative}
.add-cart{position:absolute;left:62px;top:148px;width:100px;height:32px;background:#8e2a38;color:#c08a93;font-size:10px;display:flex;align-items:center;justify-content:center}
.product-label{height:62px;background:var(--berry-dim);padding:10px 14px;color:#c99aa3;position:relative}
.product.featured .product-label{background:#4e1620;color:#8a5a62}
.product-name{font-family:"Didact Gothic",sans-serif;font-size:15px}
.product-price{position:absolute;right:14px;top:11px;font-size:14px}
.product-size{font-size:9px;margin-top:4px}

/* special features */
.feature-photo{left:134px;top:1636px;width:294px;height:255px;background:linear-gradient(160deg,#8a7560 0%,#4a4f60 60%,#2e3a5a 100%)}
.features{left:450px;top:1632px;width:320px}
.features ul{list-style:none;margin-top:14px}
.features li{position:relative;padding-left:22px;font-size:11px;line-height:19px;color:#3b3b3b;margin-bottom:20px}
.features li::before{content:"";position:absolute;left:8px;top:8px;width:4px;height:4px;border-radius:50%;background:var(--berry)}
.subscribe-photo{left:773px;top:1636px;width:155px;height:255px;background:linear-gradient(120deg,#d8d8da 0%,#c9bfb8 60%,#b9aea6 100%)}
.subscribe-box{left:928px;top:1636px;width:140px;height:255px;background:var(--mustard);padding:20px 14px;color:#d9be7e}
.subscribe-box h3{font-family:"Didact Gothic",sans-serif;font-weight:400;font-size:23px;line-height:24px}
.subscribe-box .sub{font-size:11px;margin-bottom:12px}
.subscribe-box p{font-size:9px;line-height:14px}
.subscribe-field{position:absolute;left:14px;top:174px;width:110px;height:24px;background:#e2d6b8;font-size:8px;color:#6a6a6a;display:flex;align-items:center;padding-left:8px}
.subscribe-field svg{position:absolute;right:6px;top:8px}

/* footer */
.site-footer{left:0;top:1957px;width:1200px;height:273px;background:var(--footer);color:#8f6a70}
.footer-brand{left:132px;top:1995px;display:flex;align-items:center;gap:10px}
.footer-brand .brand-dot{background:#9a8a8c;width:34px;height:34px}
.footer-brand .brand-name{color:#9a8a8c;font-size:22px}
.social{left:132px;top:2080px;display:flex;gap:14px}
.social span{width:14px;height:14px;border-radius:50%;background:#9a8a8c;display:block}
.footer-col{position:absolute;top:1995px;color:#8f6a70}
.footer-col h4{font-family:"Didact Gothic",sans-serif;font-weight:400;font-size:17px;letter-spacing:.5px;color:#9a7b80;margin-bottom:14px}
.footer-col li{list-style:none;font-size:11px;line-height:20px}
.copyright{left:132px;top:2189px;font-size:10px;color:#8a5f66}

/* overlay + popup */
.dim{left:0;top:0;width:1200px;height:2230px;background:rgba(20,18,24,.12)}
.popup{left:251px;top:287px;width:698px;height:427px;background:var(--coral);box-shadow:0 6px 26px rgba(0,0,0,.35);text-align:center;color:var(--white)}
.popup h2{font-family:"Didact Gothic",sans-serif;font-weight:400;font-size:45px;line-height:52px;margin-top:62px;letter-spacing:1px;white-space:nowrap;text-shadow:0 2px 3px rgba(0,0,0,.25)}
.popup .intro{font-size:12px;margin-top:20px}
.email-field{position:absolute;left:104px;top:199px;width:488px;height:60px;background:var(--white);color:#444;font-size:13px;text-align:left;padding:21px 20px}
.popup-btn{position:absolute;top:305px;height:50px;background:var(--charcoal);color:var(--white);display:flex;flex-direction:column;align-items:center;justify-content:center;font-family:"Didact Gothic",sans-serif;letter-spacing:1px}
.btn-submit{left:152px;width:162px;font-size:19px}
.btn-decline{left:327px;width:221px;font-size:19px;line-height:19px}
.btn-decline small{font-family:"Open Sans",sans-serif;font-size:9px;letter-spacing:.4px;line-height:12px}
</style>
</head>
<body>

<!-- top bar -->
<div class="abs topbar">
  <div class="item" style="left:131px">
    <svg width="9" height="12" viewBox="0 0 9 12"><path d="M4.5 0A4.5 4.5 0 0 0 0 4.5C0 8 4.5 12 4.5 12S9 8 9 4.5A4.5 4.5 0 0 0 4.5 0zm0 6.3a1.8 1.8 0 1 1 0-3.6 1.8 1.8 0 0 1 0 3.6z"/></svg>
    <span>Moon Tot Goods, Elm Hollow, NY 00000</span>
  </div>
  <div class="item" style="left:768px">
    <svg width="11" height="11" viewBox="0 0 11 11"><path d="M2.2 0l2 2.4-1.1 1.5a7 7 0 0 0 4 4l1.5-1.1L11 8.8 9.6 11C4.4 11 0 6.6 0 1.4z"/></svg>
    <span>(555) 014-TOTS</span>
  </div>
  <div class="item" style="left:897px">
    <svg width="14" height="10" viewBox="0 0 14 10"><path d="M0 0h14v10H0zM1.3 1.3v.4L7 5.6l5.7-3.9v-.4zM1.3 3.2v5.5h11.4V3.2L7 7.1z"/></svg>
    <span>MoonTotGoods@mailbox-example.com</span>
  </div>
</div>

<!-- header -->
<header class="abs site-header"></header>
<div class="abs brand"><span class="brand-dot"></span><span class="brand-name">MOON TOT GOODS</span></div>
<div class="abs account">
  <a href="#">ACCOUNT</a><span>|</span><a href="#">YOUR CART</a>
  <span class="cart-badge"><svg width="16" height="14" viewBox="0 0 16 14" fill="#dfe8c4"><path d="M0 0h3l.6 2H16l-2 6H5l.5 1.6H14V11H4.4L2 1.4H0z"/><circle cx="5.5" cy="12.6" r="1.3"/><circle cx="12.5" cy="12.6" r="1.3"/></svg></span>
  <span>0 ITEMS</span>
</div>
<nav class="abs main-nav">
  <a class="current" href="#">HOME</a><a href="#">PRODUCTS</a><a href="#">WHY BUY FROM US</a><a href="#">BLOG</a><a href="#">CONTACT US</a>
</nav>

<!-- hero -->
<section class="abs hero" role="img" aria-label="Banner photo of a baby reaching upward on a soft light background"></section>
<div class="abs hero-copy">
  <div class="hero-kicker">WE SELL</div>
  <div class="hero-title">BABY BIBS</div>
  <div class="hero-text">100% SILICONE BIBS,<br>THEY ARE SAFE AND LIGHT,<br>SOFT, SMOOTH AND FLEXIBLE.</div>
</div>
<a class="abs btn-read" href="#">READ MORE</a>
<div class="abs slider-dots"><span></span><span></span><span></span></div>

<!-- why us -->
<h2 class="abs section-title why-title"><span class="lead">WHY</span><span class="tail">MOONTOTGOODS</span></h2>
<div class="why-col" style="left:132px"><p>Neque porro quisquam est qui dolorem ipsum quia dolor sit amet, consectetur, adipisci velit..."</p><a class="more" href="#">Learn More</a></div>
<div class="why-col" style="left:452px"><p>Neque porro quisquam est qui dolorem ipsum quia dolor sit amet, consectetur, adipisci velit..."</p><a class="more" href="#">Learn More</a></div>
<div class="why-col" style="left:772px"><p>Neque porro quisquam est qui dolorem ipsum quia dolor sit amet, consectetur, adipisci velit..."</p><a class="more" href="#">Learn More</a></div>
<div class="why-photo" style="left:132px" role="img" aria-label="Photo of a seated baby wearing a blue silicone bib"></div>
<div class="why-photo" style="left:452px" role="img" aria-label="Photo of a baby brushing teeth wearing a green silicone bib"></div>
<div class="why-photo" style="left:772px" role="img" aria-label="Photo of a seated baby wearing a yellow silicone bib"></div>

<!-- products -->
<h2 class="abs section-title products-title"><span class="lead">OUR</span> <span class="tail">PRODUCTS</span></h2>
<div class="abs carousel-arrows">
  <svg width="10" height="16" viewBox="0 0 10 16"><path d="M8 1L2 8l6 7" stroke="#222" stroke-width="2" fill="none"/></svg>
  <svg width="10" height="16" viewBox="0 0 10 16"><path d="M2 1l6 7-6 7" stroke="#222" stroke-width="2" fill="none"/></svg>
</div>

<div class="product featured" style="left:132px">
  <div class="product-photo" role="img" aria-label="Product photo of a blue silicone bib"><a class="add-cart" href="#">ADD TO CART</a></div>
  <div class="product-label"><div class="product-name">Product Name</div><div class="product-price">$ 80</div><div class="product-size">3 Mini Size</div></div>
</div>
<div class="product" style="left:370px">
  <div class="product-photo" role="img" aria-label="Product photo of a yellow silicone bib"></div>
  <div class="product-label"><div class="product-name">Product Name</div><div class="product-price">$ 80</div><div class="product-size">3 Mini Size</div></div>
</div>
<div class="product" style="left:610px">
  <div class="product-photo" role="img" aria-label="Product photo of a magenta silicone bib"></div>
  <div class="product-label"><div class="product-name">Product Name</div><div class="product-price">$ 80</div><div class="product-size">3 Mini Size</div></div>
</div>
<div class="product" style="left:845px">
  <div class="product-photo" role="img" aria-label="Product photo of a green silicone bib"></div>
  <div class="product-label"><div class="product-name">Product Name</div><div class="product-price">$ 80</div><div class="product-size">3 Mini Size</div></div>
</div>

<!-- special features -->
<div class="abs feature-photo" role="img" aria-label="Close-up photo of a baby wearing a blue silicone bib"></div>
<div class="abs features">
  <h2 class="section-title" style="font-size:27px"><span class="lead">SPECIAL</span> <span class="tail">FEATURES</span></h2>
  <ul>
    <li>The bibs are made of 100% silicon, they are safe, light weight, soft, smooth, flexible, dishwasher safe and has funny faces.</li>
    <li>The bibs are made of 100% silicon, they are safe, light weight, soft, smooth, flexible.</li>
    <li>The bibs are made of 100% silicon, they are safe, light weight, soft, smooth, flexible.</li>
    <li>The bibs are made of 100% silicon.</li>
  </ul>
</div>
<div class="abs subscribe-photo" role="img" aria-label="Photo of a smiling baby with a parent"></div>
<div class="abs subscribe-box">
  <h3>Subscribe</h3>
  <div class="sub">Newsletter</div>
  <p>Join our list for new bibs, special offers and helpful tips sent to you every month.</p>
  <div class="subscribe-field">Enter Email Id
    <svg width="9" height="7" viewBox="0 0 14 10" fill="#555"><path d="M0 0h14v10H0zM1.3 1.3v.4L7 5.6l5.7-3.9v-.4z"/></svg>
  </div>
</div>

<!-- footer -->
<footer class="abs site-footer"></footer>
<div class="abs footer-brand"><span class="brand-dot"></span><span class="brand-name">MOON TOT GOODS</span></div>
<div class="abs social">
  <a href="#" aria-label="Social link one"><span></span></a>
  <a href="#" aria-label="Social link two"><span></span></a>
  <a href="#" aria-label="Social link three"><span></span></a>
  <a href="#" aria-label="Social link four"><span></span></a>
</div>
<div class="footer-col" style="left:422px"><h4>SITEMAP</h4><ul><li>Home</li><li>Products</li><li>Why buy from us</li><li>Blog</li><li>Contact us</li></ul></div>
<div class="footer-col" style="left:687px"><h4>MOONTOTGOODS</h4><ul><li>Baby registry</li><li>Gift Cards / Wrap</li><li>Reward Program</li><li>Sale</li><li>About Us</li><li>Customer Service</li></ul></div>
<div class="footer-col" style="left:959px"><h4>WHOLESALE</h4><ul><li>Become a retailer</li><li>Login</li><li>Find a store</li></ul></div>
<div class="abs copyright">© 2016 MoonTotGoods-example.com. All rights reserved.</div>

<!-- subscription popup -->
<div class="abs dim"></div>
<div class="abs popup">
  <h2>Want 10% off your next order ?</h2>
  <p class="intro">Suscribe to our mailing list below and get a 10% off code to use at check out.</p>
  <div class="email-field">Enter Your Email Id</div>
  <a class="popup-btn btn-submit" href="#">SUBMIT</a>
  <a class="popup-btn btn-decline" href="#">NO THANK YOU<small>I WANT TO PAY FULL PRICE</small></a>
</div>

</body>
</html>
```